Website for new child psychology practice

New clinical psychology practice in NSW Australia, specialising in work with children, adolescents and families. I would like to feature the colours in the logo, which was recently designed by pixelharbor designer Odette.
I am seeking a professional looking page, which is easy to navigate and is colourful and playful but not childish.
Target Market(s)
Parents and professionals
Industry/Entity Type
Health
Coding
Coded - Design and coding required
Number of Pages Required
1 page
Font styles to use
Serif
Requirements
Must have
- Pages for 'About us' 'Services' 'Fees and information' 'Contact us'
Should not have
- Childish stock photos

```html
<!DOCTYPE html>
<html lang="en">
<head>
<meta charset="utf-8">
<title>Dr Clara Hayes – Clinical Psychologist</title>
<link href="https://fonts.googleapis.com/css2?family=Open+Sans:wght@400;600;700;800&family=Tinos:wght@400;700&display=swap" rel="stylesheet">
<style>
:root{
  --purple:#a3338f;
  --purple-dark:#7d2470;
  --navy:#1f2a6b;
  --orange:#e0611c;
  --lav:#f2eff8;
  --text:#8a8a96;
  --dark:#262a3a;
  --bar:#2f3656;
  --white:#fff;
}
*{margin:0;padding:0;box-sizing:border-box}
html,body{width:1200px;height:4566px;overflow:hidden}
body{position:relative;background:var(--white);font-family:"Open Sans",Arial,sans-serif;color:var(--text)}
.abs{position:absolute}
.serif{font-family:"Tinos","Times New Roman",serif}

/* header */
.top-icon{width:32px;height:32px;border-radius:50%;background:var(--purple)}
.top-label{font-size:12px;color:#333;font-weight:700;line-height:16px}
.top-label span{display:block;font-weight:400;color:#999;font-size:11px}
.btn-appt{left:879px;top:11px;width:183px;height:40px;border-radius:20px;background:var(--navy);color:#fff;font-size:12px;font-weight:700;display:flex;align-items:center;justify-content:center}
.nav a{position:absolute;top:84px;font-size:12px;color:#444;text-decoration:none}
.brand{font-family:"Tinos",serif;font-size:20px;color:var(--navy);letter-spacing:1px;display:flex;align-items:center;gap:8px}
.brand i{display:block;width:22px;height:22px;border-radius:50%;background:var(--purple)}

/* hero */
.hero{left:0;top:122px;width:1200px;height:764px;background:linear-gradient(100deg,#3b3560 0%,#4e4673 45%,#6b6488 100%)}
.hero-eyebrow{left:87px;top:323px;color:#fff;font-size:15px;letter-spacing:3px;font-weight:600}
.hero-title{left:87px;top:360px;color:#fff;font-size:46px;font-weight:700;line-height:58px}
.hero-rule{left:87px;top:494px;width:633px;height:1px;background:rgba(255,255,255,.6)}
.hero-text{left:87px;top:522px;width:640px;color:#fff;font-size:16px;font-weight:700;line-height:26px}
.btn{border-radius:22px;font-size:14px;font-weight:600;display:flex;align-items:center;justify-content:center;height:40px}

/* sections */
.eyebrow{font-family:"Tinos",serif;color:var(--purple);font-size:18px}
.h-main{font-family:"Tinos",serif;color:var(--purple);font-size:46px;line-height:54px;font-weight:400}
.sec-title{width:1200px;text-align:center;font-family:"Tinos",serif;color:var(--purple);font-size:46px}
.sec-sub{width:1200px;text-align:center;font-size:13.5px;line-height:23px}
.body-t{font-size:13.5px;line-height:23px}

.service{width:320px;height:270px;border-radius:6px;overflow:hidden}
.service h3{position:absolute;left:20px;top:64px;font-family:"Tinos",serif;font-weight:700;color:#fff;font-size:27px}
.svc-icon{width:72px;height:72px;border-radius:50%;background:#fff;box-shadow:0 3px 10px rgba(0,0,0,.12);display:flex;align-items:center;justify-content:center}

.why-h{font-family:"Tinos",serif;color:var(--purple);font-size:22px}
.why-t{font-size:13px;line-height:23px;width:260px}
.why-icon{width:86px;height:86px;border-radius:50%;background:var(--purple);border:5px solid #fff;box-shadow:0 0 0 2px #e8b7d9;display:flex;align-items:center;justify-content:center}

/* contact */
.contact{left:0;top:2864px;width:1200px;height:560px;background:linear-gradient(160deg,#b04a9e 0%,#9b2f8a 50%,#c56bb0 100%)}
.hours{left:98px;top:3060px;width:491px;height:234px;background:rgba(70,25,70,.55);border-left:2px solid var(--orange)}
.hours-row{position:absolute;left:34px;width:425px;display:flex;justify-content:space-between;color:#fff;font-size:15px;padding-bottom:14px;border-bottom:1px solid rgba(255,255,255,.25)}
.hours-row b{font-weight:700}
.form-card{left:612px;top:2890px;width:491px;height:500px;background:var(--lav)}
.field{position:absolute;height:52px;background:#fff;font-size:14px;color:#777;padding-left:26px;display:flex;align-items:center}
.submit{left:53px;top:424px;width:385px;height:52px;background:var(--orange);color:#fff;font-weight:700;font-size:18px;display:flex;align-items:center;justify-content:center}

/* reviews */
.reviews{left:0;top:3424px;width:1200px;height:700px;background:linear-gradient(#fff 0%,#f3f0f8 100%)}
.review{width:320px;height:270px;background:#fff;box-shadow:0 4px 16px rgba(60,40,90,.08)}
.review .avatar{position:absolute;left:28px;top:-30px;width:62px;height:62px;border-radius:50%;background:linear-gradient(#dcd4e0,#a99fb0);border:3px solid #fff}
.review .quote{position:absolute;right:30px;top:-14px;font-family:"Tinos",serif;font-size:96px;line-height:90px;font-weight:700;color:#f4c7ad}
.review .stars{position:absolute;left:28px;top:52px;color:var(--orange);font-size:17px;letter-spacing:3px}
.review p{position:absolute;left:28px;top:88px;width:270px;font-size:13px;line-height:23px}
.review .name{position:absolute;left:28px;top:196px;font-family:"Tinos",serif;color:var(--navy);font-size:20px}
.review .role{position:absolute;left:28px;top:226px;font-size:10px;color:#555}

/* footer */
.footer{left:0;top:4040px;width:1200px;height:526px}
.f-nav{position:absolute;top:4330px;color:#fff;font-size:14px;font-weight:600}
.f-ico{width:58px;height:58px;border-radius:50%;border:2px solid #fff}
.f-lbl{color:#fff;font-size:12px;font-weight:600;line-height:18px}
.social{width:26px;height:26px;border:1px solid #fff;border-radius:3px}
</style>
</head>
<body>

<!-- Header -->
<header>
  <div class="abs top-icon" style="left:122px;top:16px"></div>
  <div class="abs top-label" style="left:168px;top:18px">Call Us:<span>(203) 555-0147</span></div>
  <div class="abs top-icon" style="left:278px;top:16px"></div>
  <div class="abs top-label" style="left:326px;top:18px">Email:<span>office@clarahayes.example</span></div>
  <div class="abs btn-appt">MAKE APPOINTMENT</div>
  <div class="abs" style="left:124px;top:67px;width:358px;height:1px;background:#ddd"></div>
  <div class="abs" style="left:706px;top:67px;width:358px;height:1px;background:#ddd"></div>
  <div class="abs brand" style="left:505px;top:54px"><i></i>DR CLARA HAYES</div>
  <nav class="nav">
    <a href="#" style="left:131px">Home</a>
    <a href="#" style="left:243px">About Us</a>
    <a href="#" style="left:394px">Services</a>
    <a href="#" style="left:713px">Our Team</a>
    <a href="#" style="left:840px">Gallery</a>
    <a href="#" style="left:964px">Contact Us</a>
  </nav>
</header>

<!-- Hero -->
<section>
  <div class="abs hero" role="img" aria-label="Smiling family with a child talking to a psychologist in a bright room"></div>
  <div class="abs hero-eyebrow">CHILD PSYCHOLOGY</div>
  <h1 class="abs hero-title">Empowering You to<br>Live Your Best Life</h1>
  <div class="abs hero-rule"></div>
  <p class="abs hero-text">Lorem ipsum dolor sit amet, consectetur adipiscing elit et dolore conser tempor incididunt ut labore et dolore magna</p>
  <div class="abs btn" style="left:83px;top:611px;width:144px;background:var(--purple);color:#fff">LEARN MORE</div>
  <div class="abs btn" style="left:240px;top:611px;width:178px;background:#fff;color:#333">REQUEST QUOTE</div>
  <svg class="abs" style="left:0;top:620px" width="1200" height="330" viewBox="0 0 1200 330">
    <path d="M0,170 Q600,330 1200,120 L1200,330 L0,330 Z" fill="#fff"/>
    <path d="M230,240 Q600,290 966,240" fill="none" stroke="var(--orange)" stroke-width="5"/>
    <circle cx="600" cy="266" r="30" fill="#fff" stroke="#eee"/>
  </svg>
</section>

<!-- About -->
<section>
  <svg class="abs" style="left:76px;top:995px" width="480" height="480" viewBox="0 0 480 480">
    <circle cx="240" cy="240" r="234" fill="none" stroke="var(--purple)" stroke-width="5" stroke-dasharray="900 600" transform="rotate(-160 240 240)"/>
  </svg>
  <div class="abs" style="left:93px;top:1014px;width:446px;height:446px;border-radius:50%;background:linear-gradient(135deg,#c9c3c8,#8d8592 60%,#4d4655)" role="img" aria-label="Smiling psychologist talking with a client"></div>
  <div class="abs eyebrow" style="left:620px;top:1014px">Child Psychology</div>
  <h2 class="abs h-main" style="left:620px;top:1044px">Cultivating Confidence,<br>Igniting Change</h2>
  <div class="abs" style="left:620px;top:1167px;width:3px;height:62px;background:var(--navy)"></div>
  <p class="abs body-t" style="left:637px;top:1172px;width:450px">Lorem ipsum dolor sit amet, consectetur adipiscing elit, sed do eiusmod or incididunt ut labore et dolore</p>
  <p class="abs body-t" style="left:620px;top:1250px;width:470px">Lorem ipsum dolor sit amet, consectetur adipiscing elit, sed do eiusmod tem por incididunt ut labore et dolore magna aliqua. Ut enim ad minim veniam, quis nostrud exercitation ullamco laboris nisi ut aliquip ex ea commodo consequat. Duis aute irure dolor in reprehenderit in voluptate velit esse cillum dolore eu fugiat nulla pariatur. Excepteur</p>
  <div class="abs" style="left:619px;top:1399px;width:154px;height:46px;background:var(--orange);border-radius:3px;color:#fff;font-weight:700;font-size:15px;display:flex;align-items:center;justify-content:center;gap:10px">Learn More
    <svg width="18" height="12" viewBox="0 0 18 12"><path d="M0,6 H16 M11,1 L16,6 L11,11" stroke="#fff" stroke-width="2" fill="none"/></svg></div>
</section>

<!-- Services -->
<section>
  <div class="abs" style="left:0;top:1548px;width:1200px;height:572px;background:var(--lav)"></div>
  <h2 class="abs sec-title" style="left:0;top:1610px">Our Services</h2>
  <p class="abs sec-sub" style="left:0;top:1676px">Lorem ipsum dolor sit amet, consectetur adipiscing elit, sed do eiusmod temp<br>or incididunt ut labore et dolore</p>

  <div class="abs service" style="left:90px;top:1787px;background:linear-gradient(135deg,#5a5270,#8a7f93)" role="img" aria-label="Family therapy session photo"><h3>Family Therapy</h3></div>
  <div class="abs service" style="left:438px;top:1787px;background:linear-gradient(135deg,#4c4a66,#8b8698)" role="img" aria-label="Therapist taking notes at a table"><h3>Behavioral Intervention</h3></div>
  <div class="abs service" style="left:785px;top:1787px;background:linear-gradient(135deg,#5b5266,#3e3a50)" role="img" aria-label="Smiling client talking with a counsellor"><h3>Habit Formation</h3></div>

  <div class="abs svc-icon" style="left:134px;top:1751px"><svg width="30" height="30" viewBox="0 0 30 30"><circle cx="9" cy="8" r="3" fill="var(--orange)"/><circle cx="21" cy="8" r="3" fill="var(--orange)"/><rect x="6" y="13" width="6" height="12" fill="var(--orange)"/><rect x="18" y="13" width="6" height="12" fill="var(--orange)"/></svg></div>
  <div class="abs svc-icon" style="left:482px;top:1751px"><svg width="30" height="30" viewBox="0 0 30 30"><circle cx="15" cy="15" r="12" fill="none" stroke="var(--orange)" stroke-width="2"/><circle cx="15" cy="15" r="6" fill="none" stroke="var(--orange)" stroke-width="2"/><circle cx="15" cy="15" r="2" fill="var(--orange)"/></svg></div>
  <div class="abs svc-icon" style="left:829px;top:1751px"><svg width="30" height="30" viewBox="0 0 30 30"><circle cx="15" cy="10" r="6" fill="none" stroke="var(--orange)" stroke-width="2"/><path d="M15,16 V27 M10,27 H20" stroke="var(--orange)" stroke-width="2"/></svg></div>
</section>

<!-- Why choose us -->
<section>
  <h2 class="abs sec-title" style="left:0;top:2174px">Why Choose Us</h2>
  <p class="abs sec-sub" style="left:0;top:2240px">Lorem ipsum dolor sit amet, consectetur adipiscing elit, sed do eiusmod temp<br>or incididunt ut labore et dolore</p>
  <svg class="abs" style="left:220px;top:2350px" width="760" height="420" viewBox="0 0 760 420">
    <defs>
      <linearGradient id="wl" x1="0" x2="1"><stop offset="0" stop-color="#fff"/><stop offset="1" stop-color="#ece6f2"/></linearGradient>
      <linearGradient id="wr" x1="1" x2="0"><stop offset="0" stop-color="#fff"/><stop offset="1" stop-color="#ece6f2"/></linearGradient>
    </defs>
    <circle cx="210" cy="210" r="210" fill="url(#wl)"/>
    <circle cx="550" cy="210" r="210" fill="url(#wr)"/>
  </svg>
  <div class="abs" style="left:406px;top:2362px;width:372px;height:372px;border-radius:50%;background:linear-gradient(#4a5a8c,#2a3462)" role="img" aria-label="Smiling psychologist with arms crossed"></div>

  <div class="abs why-h" style="left:114px;top:2398px;width:260px;text-align:right">Professional</div>
  <p class="abs why-t" style="left:114px;top:2434px;text-align:right">Lorem ipsum dolor sit amet, consectet ur adipiscing elit et dolore conser</p>
  <div class="abs why-h" style="left:114px;top:2529px;width:260px;text-align:right">Innovative Solutions</div>
  <p class="abs why-t" style="left:114px;top:2565px;text-align:right">Lorem ipsum dolor sit amet, consectet ur adipiscing elit et dolore conser</p>
  <div class="abs why-h" style="left:114px;top:2662px;width:260px;text-align:right">Personal Approach</div>
  <p class="abs why-t" style="left:114px;top:2698px;text-align:right">Lorem ipsum dolor sit amet, consectet ur adipiscing elit et dolore conser</p>

  <div class="abs why-h" style="left:796px;top:2398px">Experienced Experts</div>
  <p class="abs why-t" style="left:796px;top:2434px">Lorem ipsum dolor sit amet, consectet ur adipiscing elit et dolore conser</p>
  <div class="abs why-h" style="left:796px;top:2529px">Proven Track Record</div>
  <p class="abs why-t" style="left:796px;top:2565px">Lorem ipsum dolor sit amet, consectet ur adipiscing elit et dolore conser</p>
  <div class="abs why-h" style="left:796px;top:2662px">Quality Services</div>
  <p class="abs why-t" style="left:796px;top:2698px">Lorem ipsum dolor sit amet, consectet ur adipiscing elit et dolore conser</p>

  <div class="abs why-icon" style="left:397px;top:2397px"><svg width="34" height="34" viewBox="0 0 34 34"><circle cx="17" cy="6" r="3.5" fill="#fff"/><path d="M5,13 H29 M17,12 V22 L10,31 M17,22 L24,31" stroke="#fff" stroke-width="2.5" fill="none"/></svg></div>
  <div class="abs why-icon" style="left:397px;top:2528px"><svg width="34" height="34" viewBox="0 0 34 34"><circle cx="17" cy="17" r="12" fill="none" stroke="#fff" stroke-width="3" stroke-dasharray="4 4"/></svg></div>
  <div class="abs why-icon" style="left:397px;top:2661px"><svg width="34" height="34" viewBox="0 0 34 34"><path d="M6,20 V16 A11,11 0 0 1 28,16 V20" stroke="#fff" stroke-width="2.5" fill="none"/><rect x="4" y="19" width="6" height="8" rx="2" fill="#fff"/><rect x="24" y="19" width="6" height="8" rx="2" fill="#fff"/></svg></div>
  <div class="abs why-icon" style="left:691px;top:2397px"><svg width="34" height="34" viewBox="0 0 34 34"><circle cx="17" cy="17" r="13" fill="none" stroke="#fff" stroke-width="2"/><circle cx="17" cy="17" r="7" fill="none" stroke="#fff" stroke-width="2"/><circle cx="17" cy="17" r="2.5" fill="#fff"/></svg></div>
  <div class="abs why-icon" style="left:691px;top:2528px"><svg width="34" height="34" viewBox="0 0 34 34"><path d="M6,20 V16 A11,11 0 0 1 28,16 V20" stroke="#fff" stroke-width="2.5" fill="none"/><rect x="4" y="19" width="6" height="8" rx="2" fill="#fff"/><rect x="24" y="19" width="6" height="8" rx="2" fill="#fff"/></svg></div>
  <div class="abs why-icon" style="left:691px;top:2661px"><svg width="34" height="34" viewBox="0 0 34 34"><rect x="4" y="4" width="8" height="8" fill="none" stroke="#fff" stroke-width="2"/><rect x="22" y="4" width="8" height="8" fill="none" stroke="#fff" stroke-width="2"/><rect x="4" y="22" width="8" height="8" fill="none" stroke="#fff" stroke-width="2"/><rect x="22" y="22" width="8" height="8" fill="none" stroke="#fff" stroke-width="2"/><path d="M12,8 H22 M8,12 V22 M12,26 H22" stroke="#fff" stroke-width="2"/></svg></div>
</section>

<!-- Contact -->
<section>
  <div class="abs contact" role="img" aria-label="Soft purple toned background photo"></div>
  <h3 class="abs serif" style="left:92px;top:2996px;color:#fff;font-size:27px;font-weight:400">Open Hours</h3>
  <div class="abs hours">
    <div class="hours-row" style="top:32px"><b>Monday - Friday</b><span>08am - 05pm</span></div>
    <div class="hours-row" style="top:82px"><b>Saturday</b><span>08am - 05pm</span></div>
    <div class="hours-row" style="top:134px"><b>Telephone</b><span>+61 2 5550 1478</span></div>
    <div class="hours-row" style="top:184px;border-bottom:none"><b>Email</b><span>hello@clarahayes.example</span></div>
  </div>
  <div class="abs form-card">
    <div class="abs" style="left:53px;top:42px;width:56px;height:56px;border-radius:50%;background:var(--purple);display:flex;align-items:center;justify-content:center">
      <svg width="26" height="22" viewBox="0 0 26 22"><rect x="1" y="5" width="24" height="16" fill="none" stroke="#fff" stroke-width="1.8"/><path d="M1,5 L13,14 L25,5" stroke="#fff" stroke-width="1.8" fill="none"/></svg></div>
    <h3 class="abs serif" style="left:128px;top:46px;color:var(--navy);font-size:33px;font-weight:400">Get in touch with us</h3>
    <div class="field" style="left:53px;top:136px;width:187px">First Name</div>
    <div class="field" style="left:253px;top:136px;width:185px">Last Name</div>
    <div class="field" style="left:53px;top:208px;width:187px">Email Address</div>
    <div class="field" style="left:253px;top:208px;width:185px">Phone Number</div>
    <div class="field" style="left:53px;top:280px;width:385px">Select Subject</div>
    <div class="field" style="left:53px;top:352px;width:385px">dd/mm/yyyy</div>
    <div class="abs submit">SUBMIT</div>
  </div>
</section>

<!-- Reviews -->
<section>
  <div class="abs reviews"></div>
  <h2 class="abs sec-title" style="left:0;top:3506px">Clients Reviews</h2>
  <p class="abs sec-sub" style="left:0;top:3572px">Lorem ipsum dolor sit amet, consectetur adipiscing elit, sed do eiusmod temp<br>or incididunt ut labore et dolore</p>

  <div class="abs review" style="left:101px;top:3698px">
    <div class="avatar" role="img" aria-label="Client portrait"></div><div class="quote">"</div>
    <div class="stars">★★★★★</div>
    <p>Lorem ipsum dolor sit amet, consectetur adipiscing elit, sed do eiusmod tempor inci didunt ut labore et dolore magna aliqua. Ut enim ad minim veniam, quis</p>
    <div class="name">Nina Calder</div><div class="role">BUSINESSMAN</div>
  </div>
  <div class="abs review" style="left:445px;top:3698px;border-bottom:4px solid var(--purple)">
    <div class="avatar" role="img" aria-label="Client portrait"></div><div class="quote" style="color:var(--orange)">"</div>
    <div class="stars">★★★★★</div>
    <p>Lorem ipsum dolor sit amet, consectetur adipiscing elit, sed do eiusmod tempor inci didunt ut labore et dolore magna aliqua. Ut enim ad minim veniam, quis</p>
    <div class="name">Nina Calder</div><div class="role">BUSINESSMAN</div>
  </div>
  <div class="abs review" style="left:789px;top:3698px">
    <div class="avatar" role="img" aria-label="Client portrait"></div><div class="quote">"</div>
    <div class="stars">★★★★★</div>
    <p>Lorem ipsum dolor sit amet, consectetur adipiscing elit, sed do eiusmod tempor inci didunt ut labore et dolore magna aliqua. Ut enim ad minim veniam, quis</p>
    <div class="name">Nina Calder</div><div class="role">BUSINESSMAN</div>
  </div>
</section>

<!-- Footer -->
<footer>
  <svg class="abs footer" width="1200" height="526" viewBox="0 0 1200 526">
    <path d="M0,0 Q600,120 1200,0 L1200,526 L0,526 Z" fill="var(--dark)"/>
    <path d="M230,72 Q600,100 966,72" fill="none" stroke="var(--orange)" stroke-width="5"/>
    <circle cx="600" cy="79" r="30" fill="#fff"/>
  </svg>
  <div class="abs" style="left:0;top:4250px;width:1200px;display:flex;justify-content:center">
    <div class="brand" style="color:#fff;font-size:30px;gap:12px"><i style="background:#fff;width:32px;height:32px"></i>DR CLARA HAYES</div>
  </div>
  <span class="f-nav" style="left:357px">HOME</span>
  <span class="f-nav" style="left:450px">SERVICES</span>
  <span class="f-nav" style="left:556px">ABOUT US</span>
  <span class="f-nav" style="left:675px">TESTIMONIALS</span>
  <span class="f-nav" style="left:827px">BLOG</span>
  <div class="abs" style="left:141px;top:4383px;width:918px;height:1px;background:rgba(255,255,255,.35)"></div>

  <div class="abs f-ico" style="left:172px;top:4425px"></div>
  <div class="abs f-lbl" style="left:246px;top:4436px">14 Harbour Lane, Suite 3<br>Newtown, NSW 2042</div>
  <div class="abs" style="left:429px;top:4420px;width:1px;height:64px;background:rgba(255,255,255,.35)"></div>
  <div class="abs f-ico" style="left:505px;top:4425px"></div>
  <div class="abs f-lbl" style="left:578px;top:4436px">PHONE<br>(02) 5550 1478</div>
  <div class="abs" style="left:750px;top:4420px;width:1px;height:64px;background:rgba(255,255,255,.35)"></div>
  <div class="abs f-ico" style="left:826px;top:4425px"></div>
  <div class="abs f-lbl" style="left:902px;top:4436px">EMAIL<br>hello@clarahayes.example</div>

  <div class="abs" style="left:0;top:4512px;width:1200px;height:54px;background:var(--bar)"></div>
  <div class="abs" style="left:152px;top:4530px;color:#fff;font-size:12px;font-weight:600">Dr Clara Hayes</div>
  <div class="abs social" style="left:933px;top:4526px"></div>
  <div class="abs social" style="left:965px;top:4526px"></div>
  <div class="abs social" style="left:997px;top:4526px"></div>
  <div class="abs social" style="left:1030px;top:4526px"></div>
</footer>

</body>
</html>
```